New Wix logo and website layout

I need a new logo design and a new, modern website layout design. I am a professional therapist providing remedial massage. I am Canadian but live in Australia & would like the logo to have a somewhat 'Canadian feel' to it (something subtle i.e. no flags) I currently have a maple tree leaf as my logo. my current website is tidewaterbodywork.com.au. I need the website to work on mobile phones & traditional web browsers.

Target Market(s)

customers looking for remedial massage and manual lymphatic drainage

Industry/Entity Type

professional massage

Coding

Coded - Design and coding required

Font styles to use
Sans Serif

Colors
EB3D1F
EC4F4E
F09395
F8D3D4
FCEDEE

Requirements
Nice to have
• something subtle that indicates that I am canadian
Should not have
• no flags. nothing too bold

```html
<!DOCTYPE html>
<html lang="en">
<head>
<meta charset="utf-8">
<title>Tidewater Bodywork</title>
<link href="https://fonts.googleapis.com/css2?family=Dancing+Script:wght@500;600;700&family=Rubik:wght@400;500;700&family=Raleway:wght@400;500&display=swap" rel="stylesheet">
<style>
:root{
  --red:#EB3D1F;
  --coral:#EC4F4E;
  --rose:#F09395;
  --blush:#F8D3D4;
  --mist:#FCEDEE;
  --ink:#1c1c1c;
  --text:#555;
  --footer:#1a1a1a;
  --white:#fff;
}
*{box-sizing:border-box;margin:0;padding:0}
html,body{width:1200px;height:2863px;overflow:hidden}
body{position:relative;background:var(--white);font-family:"Rubik",sans-serif;color:var(--ink)}
.abs{position:absolute}
.script{font-family:"Dancing Script",cursive}
.btn{position:absolute;display:flex;align-items:center;justify-content:center;font-family:"Dancing Script",cursive;font-weight:600;font-size:19px;border-radius:26px 2px 2px 26px;text-decoration:none}
.btn-solid{background:var(--red);color:var(--white)}
.btn-outline{border:2px solid var(--red);color:var(--red);background:transparent}

/* header */
.site-header{position:absolute;left:0;top:0;width:1200px;height:118px;background:var(--white)}
.brand{position:absolute;left:111px;top:38px;display:flex;align-items:center;gap:12px}
.brand-dot{width:40px;height:40px;border-radius:50%;background:var(--red)}
.brand-name{font-family:"Rubik",sans-serif;font-weight:700;font-size:21px;color:var(--ink);letter-spacing:.3px}
.nav a{position:absolute;top:52px;font-size:15.5px;color:var(--ink);text-decoration:none}
.login{left:961px;top:36px;width:128px;height:54px}

/* hero */
.hero{position:absolute;left:0;top:118px;width:1200px;height:600px}
.hero-photo{position:absolute;inset:0;background:
  radial-gradient(ellipse 380px 300px at 700px 240px,#f05a24 0%,#e8471e 40%,rgba(232,71,30,0) 75%),
  radial-gradient(ellipse 160px 160px at 1120px 120px,#e94a1f 0%,rgba(233,74,31,0) 80%),
  linear-gradient(180deg,#dfe0e4 0%,#d8d9dd 70%,#e9b7a8 88%,#e9603c 100%)}
.hero-title{position:absolute;left:111px;top:200px;font-family:"Dancing Script",cursive;font-weight:700;font-size:72px;line-height:78px;color:var(--red)}
.hero-cta{left:114px;top:384px;width:127px;height:55px;font-weight:500}
.dots{position:absolute;left:568px;top:555px;display:flex;gap:7px}
.dots span{width:10px;height:10px;border-radius:50%;border:1px solid #777}
.dots .on{background:var(--red);border-color:var(--red)}

/* about */
.about-photo{position:absolute;left:120px;top:800px;width:460px;height:400px;border-radius:48% 52% 40% 60%/50% 45% 55% 50%;background:radial-gradient(circle at 50% 50%,#e9a58a 0%,#dc8f76 55%,#f3d5cb 100%)}
.section-title{font-family:"Dancing Script",cursive;font-weight:500;font-size:40px;color:var(--ink)}
.about-title{position:absolute;left:648px;top:800px}
.about-text{position:absolute;left:648px;top:868px;width:399px;font-family:"Raleway",sans-serif;font-size:14px;line-height:25.6px;color:var(--text);text-align:justify}
.about-text p+p{margin-top:15px}
.about-cta{left:648px;top:1125px;width:136px;height:56px}

/* services */
.services{position:absolute;left:0;top:1267px;width:1200px;height:625px;background:linear-gradient(160deg,var(--mist) 0%,#f8e4e4 40%,var(--mist) 70%,#f6dcdc 100%)}
.services-title{position:absolute;left:0;top:78px;width:1200px;text-align:center}
.card{position:absolute;top:161px;width:230px;height:379px;background:var(--white);border-radius:4px;box-shadow:0 6px 14px rgba(0,0,0,.08);overflow:hidden;text-align:center}
.card-photo{height:173px}
.card h3{font-family:"Dancing Script",cursive;font-weight:500;font-size:23px;margin-top:14px;color:var(--ink)}
.card p{font-family:"Raleway",sans-serif;font-size:13px;line-height:21px;color:var(--text);padding:0 20px;margin-top:12px}
.card .btn{left:51px;top:306px;width:128px;height:52px}
.card.active{background:var(--red)}
.card.active h3,.card.active p{color:var(--white)}
.card.active .btn{border-color:var(--white);color:var(--white)}
.arrow{position:absolute;top:1598px;width:40px;height:40px;border-radius:50%;display:flex;align-items:center;justify-content:center}
.arrow-prev{left:37px;background:var(--red)}
.arrow-next{left:1124px;border:1.5px solid var(--ink)}

/* remedial */
.remedial-title{position:absolute;left:111px;top:2008px}
.remedial-text{position:absolute;left:111px;top:2086px;width:399px;font-family:"Raleway",sans-serif;font-size:14px;line-height:25.6px;color:var(--text);text-align:justify}
.remedial-cta{left:111px;top:2302px;width:136px;height:55px}
.remedial-ring{position:absolute;left:642px;top:1978px;width:422px;height:428px;border-radius:50%;background:var(--coral)}
.remedial-photo{position:absolute;left:642px;top:1978px;width:422px;height:422px;border-radius:50%;background:radial-gradient(circle at 45% 45%,#d08a5c 0%,#9b5a36 45%,#5a3322 100%)}
.chat{position:absolute;left:1159px;top:2430px;width:41px;height:41px;border-radius:50%;background:#2a7fd4;display:flex;align-items:center;justify-content:center}

/* footer */
.site-footer{position:absolute;left:0;top:2490px;width:1200px;height:373px;background:var(--footer);color:var(--white)}
.footer-brand{position:absolute;left:105px;top:120px;width:250px;text-align:center}
.footer-brand .brand-dot{width:90px;height:90px;margin:0 auto 20px}
.footer-brand .brand-name{color:var(--white);font-size:24px}
.footer-heading{position:absolute;top:78px;font-family:"Dancing Script",cursive;font-weight:500;font-size:26px;color:var(--white)}
.quick-links{position:absolute;left:404px;top:130px;list-style:none}
.quick-links li{font-size:15.5px;line-height:30px}
.contact-list{position:absolute;left:580px;top:140px;list-style:none;font-size:15.5px}
.contact-list li{display:flex;gap:14px;align-items:flex-start;margin-bottom:16px;line-height:26px}
.contact-list svg{flex:none;margin-top:4px}
.newsletter{position:absolute;left:864px;top:134px;width:225px;height:40px;display:flex;border-radius:5px;overflow:hidden}
.newsletter span{flex:1;background:var(--white);color:#777;font-size:15px;padding:10px 14px}
.newsletter b{width:54px;background:var(--coral);display:flex;align-items:center;justify-content:center}
.social{position:absolute;top:219px;width:42px;height:42px;border-radius:50%;background:var(--white)}
.copyright{position:absolute;left:0;top:317px;width:1200px;text-align:center;font-size:15px}
</style>
</head>
<body>

<header class="site-header">
  <div class="brand"><span class="brand-dot"></span><span class="brand-name">Tidewater Bodywork</span></div>
  <nav class="nav">
    <a style="left:428px">Home</a>
    <a style="left:505px">Remedial Massage</a>
    <a style="left:671px">About Me</a>
    <a style="left:773px">Fees</a>
    <a style="left:842px">Contact</a>
  </nav>
  <a class="btn btn-solid login">Log In</a>
</header>

<section class="hero">
  <div class="hero-photo" role="img" aria-label="Close-up of a red autumn leaf hanging over calm water with its reflection"></div>
  <h1 class="hero-title">Tidewater<br>Bodywork</h1>
  <a class="btn btn-outline hero-cta">Get Started</a>
  <div class="dots"><span></span><span class="on"></span><span></span><span></span></div>
</section>

<section class="about">
  <div class="about-photo" role="img" aria-label="Massage therapist working on a relaxed client's back, framed in a leaf shape"></div>
  <h2 class="section-title about-title">About Us</h2>
  <div class="about-text">
    <p>I completed my training in Toronto, Canada in 1999 where I obtained a Diploma of Remedial Massage through the Lakeshore College of Massage &amp; Hydrotherapy.</p>
    <p>Over the years, I have practiced in several different settings including medical centre, chiropractic clinic, spa and currently am a sole trader in my own practice. I have been helping my clients achieve better health through my treatments for several years. I take special interest in women's health.</p>
  </div>
  <a class="btn btn-solid about-cta">Learn More</a>
</section>

<section class="services">
  <h2 class="section-title services-title">Our Services</h2>
  <article class="card" style="left:112px">
    <div class="card-photo" role="img" aria-label="Herbs and a mortar with a glass bottle in a garden" style="background:linear-gradient(160deg,#4e6b2c,#8aa156 55%,#cfd8c4)"></div>
    <h3>Remedial</h3>
    <p>Lorem ipsum dolor sit amet, consectetur adipiscing elit, sed aliqua.</p>
    <a class="btn btn-outline">Learn More</a>
  </article>
  <article class="card active" style="left:361px">
    <div class="card-photo" role="img" aria-label="Hands giving a deep tissue massage on a back" style="background:linear-gradient(160deg,#3a2219,#a4674a 55%,#d69c7c)"></div>
    <h3>Deep Tissue</h3>
    <p>Lorem ipsum dolor sit amet, consectetur adipiscing elit, sed aliqua.</p>
    <a class="btn btn-outline">Learn More</a>
  </article>
  <article class="card" style="left:610px">
    <div class="card-photo" role="img" aria-label="Therapist using a fist to massage a client's back" style="background:linear-gradient(160deg,#8a6a58,#c8865a 55%,#3f5fa8)"></div>
    <h3>Therapeutic</h3>
    <p>Lorem ipsum dolor sit amet, consectetur adipiscing elit, sed aliqua.</p>
    <a class="btn btn-outline">Learn More</a>
  </article>
  <article class="card" style="left:859px">
    <div class="card-photo" role="img" aria-label="Gentle hands massaging a pregnant client's back" style="background:linear-gradient(160deg,#efe2d6,#e3b49a 55%,#f1e8e0)"></div>
    <h3>Pregnancy</h3>
    <p>Lorem ipsum dolor sit amet, consectetur adipiscing elit, sed aliqua.</p>
    <a class="btn btn-outline">Learn More</a>
  </article>
</section>
<div class="arrow arrow-prev"><svg width="14" height="14" viewBox="0 0 14 14"><path d="M9 2 4 7l5 5" fill="none" stroke="#fff" stroke-width="2"/></svg></div>
<div class="arrow arrow-next"><svg width="14" height="14" viewBox="0 0 14 14"><path d="m5 2 5 5-5 5" fill="none" stroke="#1c1c1c" stroke-width="1.6"/></svg></div>

<section class="remedial">
  <h2 class="section-title remedial-title">Remedial Massage</h2>
  <p class="remedial-text">Remedial massage is used to help relieve tension and stress in the soft tissues of the body including muscles, tendons, ligaments and connective tissue. It helps to alleviate soft tissue discomfort associated with everyday and occupational stress, over-use injuries e.g. tendinitis, and many chronic pain conditions. An increase in circulation and increased joint flexibility are additional benefits.</p>
  <a class="btn btn-solid remedial-cta">Learn More</a>
  <div class="remedial-ring"></div>
  <div class="remedial-photo" role="img" aria-label="Oiled hands massaging a client's shoulder in warm candlelight"></div>
</section>
<div class="chat"><svg width="20" height="18" viewBox="0 0 20 18"><path d="M2 2h11v8H6l-3 3v-3H2z" fill="#fff"/><path d="M15 6h3v7h-1v3l-3-3H8v-1h7z" fill="#fff"/></svg></div>

<footer class="site-footer">
  <div class="footer-brand"><div class="brand-dot"></div><div class="brand-name">Tidewater Bodywork</div></div>
  <h3 class="footer-heading" style="left:404px">Quick Links</h3>
  <ul class="quick-links">
    <li>Home</li><li>Remedial Massage</li><li>About Me</li><li>Fees</li><li>Contact</li>
  </ul>
  <h3 class="footer-heading" style="left:580px">Contact Us</h3>
  <ul class="contact-list">
    <li><svg width="16" height="20" viewBox="0 0 16 20"><path d="M8 0a7 7 0 0 0-7 7c0 5 7 13 7 13s7-8 7-13a7 7 0 0 0-7-7zm0 10a3 3 0 1 1 0-6 3 3 0 0 1 0 6z" fill="#fff"/></svg><span>Rosa Kettle 24 Ferncliff<br>Road Moorvale VIC 3199</span></li>
    <li><svg width="17" height="17" viewBox="0 0 17 17"><path d="M3.5 1 6 4 4.5 6.2a10 10 0 0 0 6.3 6.3L13 11l3 2.5-1.6 2.6C8 16 1 9 .9 2.6z" fill="#fff"/></svg><span>0400 555 187</span></li>
    <li><svg width="17" height="13" viewBox="0 0 17 13"><path d="M0 0h17v13H0z" fill="#fff"/><path d="m0 0 8.5 7L17 0" fill="none" stroke="#1a1a1a" stroke-width="1.5"/></svg><span>rosa@tidewaterbodywork.com.au</span></li>
  </ul>
  <h3 class="footer-heading" style="left:864px">Newsletter</h3>
  <div class="newsletter"><span>Enter email</span><b><svg width="16" height="12" viewBox="0 0 16 12"><path d="M0 0h16v12H0z" fill="#fff"/><path d="m0 0 8 6 8-6" fill="none" stroke="#EC4F4E" stroke-width="1.5"/></svg></b></div>
  <span class="social" style="left:883px" aria-label="Social link"></span>
  <span class="social" style="left:938px" aria-label="Social link"></span>
  <span class="social" style="left:991px" aria-label="Social link"></span>
  <span class="social" style="left:1047px" aria-label="Social link"></span>
  <p class="copyright">©Copyrights 2022 Tidewater Bodywork &nbsp;&nbsp;|&nbsp;&nbsp; All Rights Reserved</p>
</footer>

</body>
</html>
```